Business Card for Multi-Brand Sportswear Company

We are looking for a business card which represents our company and the multiple brands within it.

The company: Fen Athletics (LTD)
The brands: Fen, TavaPuni, ElmStretch, Grit and Rain

Employees using these cards would be representing Fen Athletics, rather than any of the individual brands. You will see a current design within the uploaded files, to give some inspiration. The actual text of the brands is not necessary, but the logos should be on there is some format.

Our creative minds on this are stretched, so we are looking for someone to make this their own, and show us what a good business card should look like.

We may like to get these printed with spot gloss, so keep that in mind with your designs.

www.fenathletics.co.uk

Industry/Entity Type

Business

Contact Information for Business Card

Leo Pemberton-Hale
Operations Manager
(+44) 1632 960 418
Leo@fenathletics.co.uk
www.fenathletics.co.uk

Font styles to use
Sans Serif
Other font styles liked:
• Eurostile

Colors
ffffff

Requirements
Nice to have
• Dark (black) background

```html
<!DOCTYPE html>
<html lang="en">
<head>
<meta charset="utf-8">
<title>Fen Athletics – Business Card</title>
<link rel="stylesheet" href="https://fonts.googleapis.com/css2?family=Saira+Semi+Condensed:wght@400;600&family=Oswald:wght@600&family=Open+Sans:wght@400&display=swap">
<style>
  :root {
    --bg: #2b2b2d;
    --card: #000000;
    --red: #e31e26;
    --grey: #5a5a5c;
    --white: #ffffff;
    --muted: #bdbdbd;
  }
  * { box-sizing: border-box; margin: 0; padding: 0; }
  html, body { width: 1200px; height: 1000px; overflow: hidden; }
  body {
    background: var(--bg);
    position: relative;
    font-family: "Open Sans", sans-serif;
  }
  .card {
    position: absolute;
    left: 300px;
    width: 600px;
    height: 343px;
    border-radius: 26px;
    background: var(--card);
    overflow: hidden;
  }
  .card--front { top: 110px; }
  .card--back { top: 547px; }
  .card__bands { position: absolute; inset: 0; }

  /* front */
  .wordmark {
    position: absolute;
    left: 0; right: 0; top: 128px;
    text-align: center;
    color: var(--white);
  }
  .wordmark__name {
    font-family: "Saira Semi Condensed", sans-serif;
    font-weight: 600;
    font-size: 58px;
    letter-spacing: 2px;
    line-height: 1;
    text-transform: uppercase;
  }
  .wordmark__tagline {
    font-family: "Saira Semi Condensed", sans-serif;
    font-weight: 400;
    font-size: 12px;
    letter-spacing: 4px;
    margin-top: 8px;
    text-transform: uppercase;
  }

  /* back */
  .brand-row {
    position: absolute;
    left: 0; right: 0; top: 86px;
    display: flex;
    justify-content: center;
    align-items: center;
    gap: 26px;
  }
  .brand {
    font-family: "Saira Semi Condensed", sans-serif;
    font-weight: 600;
    font-size: 17px;
    color: var(--white);
    letter-spacing: 0.5px;
  }
  .brand--muted { color: var(--muted); }
  .brand--red { color: var(--red); }
  .holder {
    position: absolute;
    left: 100px; top: 238px;
    color: var(--white);
    text-align: right;
    width: 260px;
  }
  .holder__name {
    font-family: "Oswald", sans-serif;
    font-weight: 600;
    font-size: 26px;
    line-height: 1;
    letter-spacing: 0.5px;
    text-transform: uppercase;
  }
  .holder__role {
    font-family: "Open Sans", sans-serif;
    font-size: 14px;
    margin-top: 4px;
  }
  .contact {
    position: absolute;
    left: 406px; top: 172px;
    color: var(--white);
    font-size: 11.5px;
    line-height: 1;
    list-style: none;
  }
  .contact li {
    display: flex;
    align-items: center;
    gap: 8px;
    height: 21px;
  }
  .contact svg { width: 11px; height: 11px; flex: none; }
  .contact__address { padding-left: 0; }
</style>
</head>
<body>

  <section class="card card--front" aria-label="Business card front">
    <svg class="card__bands" viewBox="0 0 600 343" aria-hidden="true">
      <polygon points="0,0 270,0 252,20 0,20" fill="var(--red)"/>
      <polygon points="270,0 600,0 600,20 252,20" fill="var(--grey)"/>
      <polygon points="0,323 348,323 330,343 0,343" fill="var(--grey)"/>
      <polygon points="348,323 600,323 600,343 330,343" fill="var(--red)"/>
    </svg>
    <div class="wordmark">
      <div class="wordmark__name">Fen Athletics</div>
      <div class="wordmark__tagline">Performance Wear</div>
    </div>
  </section>

  <section class="card card--back" aria-label="Business card back">
    <svg class="card__bands" viewBox="0 0 600 343" aria-hidden="true">
      <polygon points="0,222 392,222 392,312 0,312" fill="var(--grey)"/>
      <polygon points="392,158 600,158 600,268 392,268" fill="var(--red)"/>
    </svg>

    <div class="brand-row">
      <span class="brand brand--red">Grit and Rain</span>
      <span class="brand brand--muted">ElmStretch</span>
      <span class="brand">Fen</span>
      <span class="brand brand--muted">TavaPuni</span>
    </div>

    <div class="holder">
      <div class="holder__name">Leo Pemberton-Hale</div>
      <div class="holder__role">Managing Director</div>
    </div>

    <ul class="contact">
      <li class="contact__address">Marsh Lane, Elmworth, Fenby, YO99 1ZZ</li>
      <li>
        <svg viewBox="0 0 12 12" aria-hidden="true"><path d="M2.5 1 L4.5 1 L5.2 3.6 L4 4.6 C4.6 6 5.9 7.4 7.4 8 L8.4 6.8 L11 7.5 L11 9.5 C11 10.3 10.3 11 9.5 11 C5 11 1 7 1 2.5 C1 1.7 1.7 1 2.5 1Z" fill="var(--white)"/></svg>
        +44(0)1632 960418
      </li>
      <li>
        <svg viewBox="0 0 12 12" aria-hidden="true"><rect x="0.5" y="2" width="11" height="8" fill="var(--white)"/><path d="M0.5 2 L6 6.5 L11.5 2" fill="none" stroke="var(--red)" stroke-width="1"/></svg>
        leo@fenathletics.co.uk
      </li>
      <li>
        <svg viewBox="0 0 12 12" aria-hidden="true"><circle cx="6" cy="6" r="5.5" fill="var(--white)"/><path d="M0.5 6 H11.5 M6 0.5 C3.5 3 3.5 9 6 11.5 M6 0.5 C8.5 3 8.5 9 6 11.5" fill="none" stroke="var(--red)" stroke-width="0.8"/></svg>
        www.fenathletics.co.uk
      </li>
    </ul>
  </section>

</body>
</html>
```